Business Card Design For Office Furniture Clearance Company

Kestrel Office Clearance - our company name pretty much explains what we do, we clear offices for high end clients, mainly plc's and large international companies.

We require a nice looking business card that displays professionalism but without being too serious.

It would be nice to see just a little more than a conventional boring business card, make sure you add some flare.

Industry/Entity Type

Office Furniture

Contact Information for Business Card

CARD 1

Mark Holloway
Director
mark@kestrelofficeclearance.co.uk
m: 07700 153928

t: 01632 960418
www.kestrelofficeclearance.co.uk

Kestrel Office Clearance
Unit K4 B
2-8 Fenwick Lane
Harnwick
Aldbury Vale
ZZ9 4QT

free office clearances… you cant get better than that.

CARD 2

Peter Radford
Director
peter@kestrelofficeclearance.co.uk
m: 07700 382615

t: 01632 960418

Kestrel Office Clearance
Unit K4 B
2-8 Fenwick Lane
Harnwick
Aldbury Vale
ZZ9 4QT

Font styles to use
Sans Serif

Requirements
Must have
• A white background - as we have a blue logo.
Nice to have
• Nice use of the logo - play around with this and dissect it.

```html
<!DOCTYPE html>
<html lang="en">
<head>
<meta charset="utf-8">
<title>Kestrel Office Clearance – Business Card</title>
<link rel="stylesheet" href="https://fonts.googleapis.com/css2?family=Open+Sans:wght@400;600;700&display=swap">
<style>
  :root {
    --blue: #1b7fc4;
    --blue-deep: #136aa8;
    --blue-light: #5fa9dc;
    --ink: #3a3a3a;
    --rule: #c9cdd1;
    --paper: #ffffff;
    --paper-shade: #eceef0;
    --stage: #e6e8eb;
  }
  * { box-sizing: border-box; margin: 0; padding: 0; }
  html, body { width: 1200px; height: 843px; overflow: hidden; }
  body {
    background: var(--stage);
    font-family: "Open Sans", sans-serif;
    position: relative;
  }
  .card {
    position: absolute;
    top: 266px;
    width: 540px;
    height: 310px;
    overflow: hidden;
    box-shadow: 0 10px 28px rgba(0,0,0,.18);
  }
  /* Back of card */
  .card--back {
    left: 40px;
    background: linear-gradient(135deg, var(--blue-light) 0%, var(--blue) 45%, var(--blue-deep) 100%);
  }
  .back-mark {
    position: absolute;
    left: 50%; top: 44%;
    transform: translate(-50%, -50%);
    display: flex; flex-direction: column; align-items: center; gap: 12px;
  }
  .back-mark .dot {
    width: 130px; height: 130px; border-radius: 50%;
    background: var(--paper);
  }
  .back-mark .name {
    color: var(--paper); font-weight: 600; font-size: 15px; white-space: nowrap;
  }
  .tagline {
    position: absolute; left: 0; right: 0; bottom: 34px;
    text-align: center; color: var(--paper);
    font-size: 14px; letter-spacing: .3px;
  }
  /* Front of card */
  .card--front {
    left: 620px;
    background: linear-gradient(160deg, var(--paper) 55%, var(--paper-shade) 100%);
  }
  .front-mark {
    position: absolute; left: 42px; top: 42px;
    width: 170px;
    display: flex; flex-direction: column; align-items: center; gap: 10px;
  }
  .front-mark .dot {
    width: 150px; height: 150px; border-radius: 50%;
    background: radial-gradient(circle at 40% 40%, var(--blue-light), var(--blue) 70%);
  }
  .front-mark .name { color: var(--blue); font-weight: 600; font-size: 12px; white-space: nowrap; }
  .divider {
    position: absolute; left: 240px; top: 58px;
    width: 1px; height: 168px;
    background: var(--rule);
  }
  .contact {
    position: absolute; left: 256px; top: 60px;
    color: var(--ink); font-size: 13px; line-height: 1.35;
    white-space: nowrap;
  }
  .contact .person { color: var(--blue); font-weight: 600; font-size: 19px; line-height: 1.1; }
  .contact .role { font-size: 12px; margin-bottom: 8px; }
  .contact .company { color: var(--blue); font-weight: 700; font-size: 13px; }
  .contact .line { display: flex; align-items: center; gap: 7px; }
  .contact .line svg { width: 12px; height: 12px; fill: var(--blue); flex: none; }
  .contact .address { margin-bottom: 4px; }
  .web-band {
    position: absolute; left: 0; right: 0; top: 248px; height: 28px;
    background: var(--blue);
    display: flex; align-items: center; justify-content: space-between;
    padding: 0 22px 0 26px;
  }
  .web-band .url { color: var(--paper); font-size: 13px; letter-spacing: 1.2px; }
  .web-band .dot { width: 18px; height: 18px; border-radius: 50%; background: var(--paper); }
  .base-band {
    position: absolute; left: 0; right: 0; top: 286px; height: 8px;
    background: var(--blue);
  }
</style>
</head>
<body>

<section class="card card--back" aria-label="Card back">
  <div class="back-mark">
    <div class="dot"></div>
    <span class="name">Kestrel Office Clearance</span>
  </div>
  <p class="tagline">Office clearances at no cost… simple as that.</p>
</section>

<section class="card card--front" aria-label="Card front">
  <div class="front-mark">
    <div class="dot"></div>
    <span class="name">Kestrel Office Clearance</span>
  </div>
  <div class="divider"></div>
  <div class="contact">
    <p class="person">Mark Holloway</p>
    <p class="role">Director</p>
    <p class="company">Kestrel Office Clearance</p>
    <div class="address">
      <p>Unit K4 B, 2-8 Fenwick Lane</p>
      <p>Harnwick, Aldbury Vale, ZZ9 4QT</p>
    </div>
    <p class="line">
      <svg viewBox="0 0 24 24" aria-hidden="true"><path d="M6.6 10.8a15.1 15.1 0 0 0 6.6 6.6l2.2-2.2c.3-.3.7-.4 1-.2 1.1.4 2.3.6 3.6.6.6 0 1 .4 1 1V20c0 .6-.4 1-1 1C10.6 21 3 13.4 3 4c0-.6.4-1 1-1h3.5c.6 0 1 .4 1 1 0 1.3.2 2.5.6 3.6.1.3 0 .7-.2 1z"/></svg>
      01632 960418
    </p>
    <p class="line">
      <svg viewBox="0 0 24 24" aria-hidden="true"><path d="M7 1h10a2 2 0 0 1 2 2v18a2 2 0 0 1-2 2H7a2 2 0 0 1-2-2V3a2 2 0 0 1 2-2zm0 3v14h10V4zm5 15.5a1 1 0 1 0 0 2 1 1 0 0 0 0-2z"/></svg>
      07700 153928
    </p>
    <p class="line">
      <svg viewBox="0 0 24 24" aria-hidden="true"><path d="M2 5h20v14H2zm2 2v.5l8 5 8-5V7zm0 2.8V17h16V9.8l-8 5z"/></svg>
      mark@kestrelofficeclearance.co.uk
    </p>
  </div>
  <div class="web-band">
    <span class="url">www.kestrelofficeclearance.co.uk</span>
    <span class="dot"></span>
  </div>
  <div class="base-band"></div>
</section>

</body>
</html>
```